North Carolina-themed postcard

Would like 3x distinct designs for a postcard (sized 4.5 x 5.5) that celebrates the state of North Carolina. A vintage theme, a modern theme, and a simple black/white theme would be suggestions for design styles.

```html
<!DOCTYPE html>
<html lang="en">
<head>
<meta charset="utf-8">
<title>Greetings from North Carolina – Postcard</title>
<link href="https://fonts.googleapis.com/css2?family=Great+Vibes&family=Bungee&family=Open+Sans:wght@600&display=swap" rel="stylesheet">
<style>
  :root {
    --backdrop: #d5d5d5;
    --navy: #1d679c;
    --navy-deep: #154e78;
    --panel-light: #eef5fb;
    --panel-mid: #a9cfe8;
    --strip-pale: #c2d7ec;
    --sky-blue: #3b6fd0;
    --stone-gold: #d8b36a;
    --ink: #1f2a44;
    --rule: #2b2f36;
    --accent-red: #d8343f;
    --back-top: #a7d0ea;
    --back-bottom: #dcebf5;
    --white: #ffffff;
  }
  * { box-sizing: border-box; margin: 0; padding: 0; }
  html, body { width: 1200px; height: 696px; overflow: hidden; }
  body { background: var(--backdrop); position: relative; font-family: "Open Sans", sans-serif; }

  .postcard {
    position: absolute;
    top: 168px;
    width: 540px;
    height: 360px;
    border: 2px solid var(--rule);
    overflow: hidden;
  }
  .postcard--back { left: 40px; }
  .postcard--front { left: 620px; }

  /* Back side */
  .back-scene {
    position: absolute; inset: 0;
    background: linear-gradient(180deg, var(--back-top), var(--back-bottom) 70%, var(--back-top));
  }
  .back-band {
    position: absolute; left: 0; right: 0; bottom: 0; height: 10px;
    background: var(--navy);
  }
  .back-divider {
    position: absolute; left: 300px; top: 34px; height: 290px;
    border-left: 1.5px solid var(--rule);
  }
  .stamp-box {
    position: absolute; right: 36px; top: 56px; width: 100px; height: 60px;
    border: 1.5px solid var(--rule);
  }
  .address-line {
    position: absolute; left: 320px; right: 36px;
    border-top: 1.5px solid var(--rule);
  }

  /* Front side */
  .front-art { position: absolute; inset: 0; }
  .front-caption {
    position: absolute; top: 30px; right: 24px; width: 200px;
    color: var(--white); font-size: 12px; font-weight: 600; text-align: center;
  }
  .greeting {
    position: absolute; left: 40px; top: 112px;
    font-family: "Great Vibes", cursive; font-size: 48px; font-weight: 400; line-height: 0.95;
    color: var(--ink);
    transform: rotate(-22deg); transform-origin: left top;
    white-space: nowrap;
  }
  .greeting__from { display: block; padding-left: 90px; color: var(--accent-red); }
  .state-name {
    position: absolute; left: 36px; top: 196px; width: 280px;
    font-family: "Bungee", sans-serif; font-size: 44px; line-height: 1.05;
    text-align: center;
    color: var(--navy-deep);
    text-shadow: 2px 3px 0 var(--accent-red);
    transform: rotate(-10deg);
  }
  .state-name span { display: block; }
</style>
</head>
<body>

  <section class="postcard postcard--back" aria-label="Postcard back">
    <div class="back-scene" role="img" aria-label="Faded photograph of the State Capitol building with statue"></div>
    <div class="back-band"></div>
    <div class="back-divider"></div>
    <div class="stamp-box"></div>
    <div class="address-line" style="top:150px"></div>
    <div class="address-line" style="top:186px"></div>
    <div class="address-line" style="top:222px"></div>
    <div class="address-line" style="top:258px"></div>
  </section>

  <section class="postcard postcard--front" aria-label="Postcard front">
    <svg class="front-art" width="540" height="360" viewBox="0 0 540 360">
      <defs>
        <linearGradient id="panelGlow" x1="0" y1="0" x2="1" y2="1">
          <stop offset="0" stop-color="var(--panel-light)"/>
          <stop offset="1" stop-color="var(--panel-mid)"/>
        </linearGradient>
        <linearGradient id="capitolPhoto" x1="0" y1="0" x2="0" y2="1">
          <stop offset="0" stop-color="var(--sky-blue)"/>
          <stop offset="0.35" stop-color="var(--stone-gold)"/>
          <stop offset="1" stop-color="#8a6a3a"/>
        </linearGradient>
      </defs>
      <rect width="540" height="360" fill="var(--navy)"/>
      <polygon points="300,0 335,0 500,360 400,360" fill="var(--strip-pale)"/>
      <g role="img" aria-label="Photograph of the State Capitol in Raleigh with bronze statue">
        <polygon points="335,0 540,0 540,360 500,360" fill="url(#capitolPhoto)"/>
      </g>
      <polygon points="22,44 190,20 270,30 300,70 318,330 28,342" fill="url(#panelGlow)"/>
      <g role="img" aria-label="Illustration of a red cardinal with dogwood blossoms">
        <ellipse cx="272" cy="92" rx="24" ry="30" fill="var(--accent-red)" opacity="0.75"/>
      </g>
    </svg>
    <p class="front-caption">State Capitol In Raleigh</p>
    <h1 class="greeting">Greetings<span class="greeting__from">from</span></h1>
    <p class="state-name" role="img" aria-label="North Carolina lettering filled with city photographs"><span>North</span><span>Carolina</span></p>
  </section>

</body>
</html>
```